Need a stunning home page for Car rental company

For a client, I need a slick and sumber home page design. It is a small, local car rental company, with a handful of cars available for rent.
Selling points: affordable lease, availability, always clean cars
The design should be:
- flat and modern
- no, or very few animations/sliders
- CTA: booking form for renting a car.
- 3 featured cars with images and facts (see website) with button to read more about the car.
- fullscreen background video can be an option
- main colour: #efba01
The site is under construction here:
http://solvikutleie.hammerlia.no/
Delivery requirements:
I need a layered & well organised PSD file delivered.

```html
<!DOCTYPE html>
<html lang="en">
<head>
<meta charset="utf-8">
<title>Solvikbil – Car Rental</title>
<link href="https://fonts.googleapis.com/css2?family=Open+Sans:ital,wght@0,400;0,600;0,700;1,400&family=Bebas+Neue&family=Exo+2:wght@800&display=swap" rel="stylesheet">
<style>
:root{
  --brand:#efba01;
  --brand-dark:#6b5200;
  --ink:#222;
  --text:#444;
  --muted:#555;
  --panel:#f2f2f2;
  --accent-red:#a3141b;
  --footer:#2c2c2c;
  --white:#fff;
}
*{box-sizing:border-box;margin:0;padding:0}
html,body{width:875px;height:1200px;overflow:hidden;background:var(--white)}
body{position:relative;font-family:"Open Sans",sans-serif;color:var(--text)}
.topbar{position:absolute;left:0;top:0;width:875px;height:46px;background:var(--brand)}
.topbar__phone{position:absolute;left:38px;top:17px;font-size:9.5px;font-weight:700;color:var(--white);letter-spacing:.2px}
.social{position:absolute;display:flex;gap:13px}
.social span{width:9px;height:9px;border-radius:50%;background:var(--white)}
.topbar .social{right:42px;top:19px}
.header{position:absolute;left:0;top:46px;width:875px;height:64px;background:var(--white)}
.brand{position:absolute;left:38px;top:24px;font-size:18px;font-weight:700;color:var(--brand);letter-spacing:.5px}
.nav{position:absolute;right:38px;top:31px;display:flex;gap:41px;font-size:11px;color:#333}
.nav a{color:inherit;text-decoration:none}
.nav a.is-active{color:var(--brand)}
.hero{position:absolute;left:0;top:110px;width:875px;height:335px;overflow:hidden}
.hero__media{position:absolute;inset:0;background:linear-gradient(160deg,#6f7a2a 0%,#b59f22 30%,#7a9a2e 55%,#4e6b22 75%,#3c4a2a 100%)}
.hero__road{position:absolute;left:0;right:0;bottom:0;height:90px;background:linear-gradient(180deg,rgba(70,70,70,0) 0%,rgba(60,60,65,.8) 100%)}
.hero__title{position:absolute;left:106px;top:88px;font-family:"Bebas Neue",sans-serif;font-size:84px;line-height:1;color:var(--white)}
.hero__sub{position:absolute;left:117px;top:170px;font-size:11px;font-weight:600;color:var(--white)}
.btn{display:inline-block;font-family:"Bebas Neue",sans-serif;color:var(--white);background:var(--brand);text-align:center;border-bottom:3px solid var(--brand-dark);border-radius:2px}
.hero__cta{position:absolute;left:115px;top:203px;width:95px;height:48px;line-height:47px;font-size:19px;border-bottom-color:#b08900}
.hero__play{position:absolute;left:399px;top:142px}
.hero__dots{position:absolute;left:416px;top:307px;display:flex;gap:8px}
.hero__dots span{width:8px;height:8px;border:1px solid var(--white);border-radius:50%}
.hero__dots span.is-active{background:radial-gradient(circle,var(--white) 40%,transparent 45%)}
.intro{position:absolute;left:0;top:474px;width:875px;text-align:center}
.intro h1{font-family:"Exo 2",sans-serif;font-weight:800;font-size:21px;color:var(--ink);letter-spacing:.3px}
.intro__tag{margin-top:10px;font-style:italic;font-size:11.5px;color:#333}
.intro p.intro__text{margin:11px auto 0;width:800px;font-size:8.6px;line-height:15px;color:var(--muted)}
.section-title{position:absolute;left:38px;top:606px;font-family:"Exo 2",sans-serif;font-weight:800;font-size:21px;color:var(--ink)}
.card{position:absolute;top:655px;width:244px;height:440px;background:var(--white);box-shadow:0 0 3px rgba(0,0,0,.25);padding:6px}
.card__inner{position:relative;height:100%;background:var(--panel)}
.card__photo{position:absolute;left:10px;right:10px;top:18px;height:110px;border-radius:40% 40% 12px 12px}
.card__name{position:absolute;left:0;right:0;top:139px;text-align:center;font-size:17px;color:var(--accent-red)}
.card__price{position:absolute;left:0;right:0;top:171px;text-align:center;font-size:14.5px;color:#222}
.specs{position:absolute;left:40px;top:206px;width:170px;border-collapse:collapse;font-size:10.3px;color:#333}
.specs td{height:22.4px;padding:0}
.specs td+td{text-align:center;width:60px}
.card__btn{position:absolute;left:64px;top:375px;width:83px;height:36px;line-height:34px;font-size:16px}
.footer{position:absolute;left:0;top:1119px;width:875px;height:81px;background:var(--footer)}
.footer__nav{position:absolute;left:36px;top:28px;display:flex;gap:31px;font-size:8px;color:var(--white)}
.footer__nav a{color:inherit;text-decoration:none}
.footer__copy{position:absolute;left:37px;top:45px;font-size:8.6px;color:#ddd}
.footer .social{right:42px;top:31px}
</style>
</head>
<body>
<div class="topbar">
  <div class="topbar__phone">SPØRSMÅL? RING OSS&nbsp; 41235678</div>
  <div class="social" aria-label="Social links"><span></span><span></span><span></span><span></span><span></span><span></span><span></span></div>
</div>

<header class="header">
  <div class="brand">SOLVIKBILUTLEIE</div>
  <nav class="nav">
    <a class="is-active" href="#">HOME</a><a href="#">ABOUT US</a><a href="#">SERVICES</a><a href="#">FEATURED CARS</a><a href="#">BOOK</a><a href="#">CONTACT US</a>
  </nav>
</header>

<section class="hero">
  <div class="hero__media" role="img" aria-label="Silver sedan on a country road lined with sunlit green trees"><div class="hero__road"></div></div>
  <div class="hero__title">15% OFF</div>
  <div class="hero__sub">FROM NOW TILL 28 FEBRUARY 2015</div>
  <a class="btn hero__cta" href="#">BOOK NOW</a>
  <svg class="hero__play" width="77" height="77" viewBox="0 0 77 77" aria-label="Play video">
    <circle cx="38.5" cy="38.5" r="35" fill="none" stroke="#fff" stroke-width="5"/>
    <path d="M29 22 L56 38.5 L29 55 Z" fill="#fff"/>
  </svg>
  <div class="hero__dots"><span></span><span class="is-active"></span><span></span></div>
</section>

<section class="intro">
  <h1>WELCOME TO SOLVIKBIL</h1>
  <div class="intro__tag">We are car rental company</div>
  <p class="intro__text">Solvik car is a fleet of Solvik and rent vans and cars for people who need a ekstrabil relocation, vacation, city tour or whatever. We beat the service, and most likely also the price. And you can trust that the car you get from us is both clean and pretty!</p>
</section>

<h2 class="section-title">FEATURED CARS</h2>

<article class="card" style="left:37px">
  <div class="card__inner">
    <div class="card__photo" role="img" aria-label="Red saloon car" style="background:linear-gradient(180deg,#f2f2f2 15%,#c42a2e 45%,#7a1518 80%,#f2f2f2 100%)"></div>
    <div class="card__name">CAR</div>
    <div class="card__price">PRICE PER DAY £ 600</div>
    <table class="specs"><tr><td>CAR TYPE</td><td>CAR</td></tr><tr><td>MAX. PERS.</td><td>2</td></tr><tr><td>ANT. DOORS</td><td>5</td></tr><tr><td>MIN. DRIVER AGE</td><td>21</td></tr><tr><td>GEARBOX</td><td>MANUAL</td></tr><tr><td>AIR CONDITIONING?</td><td>YES</td></tr><tr><td>UNLIMITED KM?</td><td>NO</td></tr></table>
    <a class="btn card__btn" href="#">READ MORE</a>
  </div>
</article>

<article class="card" style="left:316px">
  <div class="card__inner">
    <div class="card__photo" role="img" aria-label="Silver coupe sedan" style="background:linear-gradient(180deg,#f2f2f2 15%,#b8b8bb 45%,#5e6064 80%,#f2f2f2 100%)"></div>
    <div class="card__name">CAR</div>
    <div class="card__price">PRICE PER DAY £ 600</div>
    <table class="specs"><tr><td>CAR TYPE</td><td>CAR</td></tr><tr><td>MAX. PERS.</td><td>2</td></tr><tr><td>ANT. DOORS</td><td>5</td></tr><tr><td>MIN. DRIVER AGE</td><td>21</td></tr><tr><td>GEARBOX</td><td>MANUAL</td></tr><tr><td>AIR CONDITIONING?</td><td>YES</td></tr><tr><td>UNLIMITED KM?</td><td>NO</td></tr></table>
    <a class="btn card__btn" href="#">READ MORE</a>
  </div>
</article>

<article class="card" style="left:593px">
  <div class="card__inner">
    <div class="card__photo" role="img" aria-label="Blue hatchback car" style="background:linear-gradient(180deg,#f2f2f2 15%,#5a8fbf 45%,#2b4a68 80%,#f2f2f2 100%)"></div>
    <div class="card__name" style="top:142px">CAR</div>
    <div class="card__price" style="top:167px">PRICE PER DAY £ 600</div>
    <table class="specs"><tr><td>CAR TYPE</td><td>CAR</td></tr><tr><td>MAX. PERS.</td><td>2</td></tr><tr><td>ANT. DOORS</td><td>5</td></tr><tr><td>MIN. DRIVER AGE</td><td>21</td></tr><tr><td>GEARBOX</td><td>MANUAL</td></tr><tr><td>AIR CONDITIONING?</td><td>YES</td></tr><tr><td>UNLIMITED KM?</td><td>NO</td></tr></table>
    <a class="btn card__btn" href="#" style="top:379px">READ MORE</a>
  </div>
</article>

<footer class="footer">
  <nav class="footer__nav"><a href="#">HOME</a><a href="#">ABOUT US</a><a href="#">SERVICES</a><a href="#">FEATURED CARS</a><a href="#">BOOK</a><a href="#">CONTACT US</a></nav>
  <div class="footer__copy">© 2014 solvikbil. All right reserved.</div>
  <div class="social" aria-label="Social links"><span></span><span></span><span></span><span></span><span></span><span></span><span></span></div>
</footer>
</body>
</html>
```